Business Card Design for a Personal Trainer

I need a business card design for my job as a personal trainer. It should have a unique, modern and exclusive design. On the front there should be only my logo with my name and my job. 0162/3819204 Tobias Lendhart Wiesengrundweg 14 80417 Munich Germany The most important contact information is the web adress. it can be bigger than the rest, but its not necessary. The card should be 8,5cmx5,5cm big. Font: Roboto. Colors: black, white, gray, 56c1ff.

```html
<!DOCTYPE html>
<html lang="de">
<head>
<meta charset="utf-8">
<title>Tobias Lendhart – Personal Trainer Business Card</title>
<link href="https://fonts.googleapis.com/css2?family=Roboto:wght@300;400;500&display=swap" rel="stylesheet">
<style>
  :root {
    --backdrop: #1c1c1e;
    --card: #0e0e10;
    --card-edge: #232326;
    --silver: #d6d6d8;
    --grey-text: #a9a9ad;
    --photo-light: #8c8c8f;
    --photo-dark: #5e5e61;
    --accent: #56c1ff;
  }
  * { box-sizing: border-box; margin: 0; padding: 0; }
  html, body {
    width: 1200px;
    height: 900px;
    overflow: hidden;
    background: var(--backdrop);
    font-family: "Roboto", Arial, sans-serif;
  }
  .stage {
    position: relative;
    width: 1200px;
    height: 900px;
  }
  .card {
    position: absolute;
    left: 340px;
    width: 520px;
    height: 336px;
    background: var(--card);
    border-radius: 22px;
    border: 1px solid var(--card-edge);
    box-shadow: 0 18px 40px rgba(0,0,0,0.55);
  }
  .card--front { top: 94px; }
  .card--back { top: 470px; }

  /* Front: name lockup */
  .lockup {
    position: absolute;
    inset: 0;
    display: flex;
    flex-direction: column;
    align-items: center;
    justify-content: center;
    gap: 10px;
  }
  .lockup__name {
    display: flex;
    align-items: center;
    gap: 14px;
    font-size: 34px;
    font-weight: 400;
    letter-spacing: 2px;
    color: var(--silver);
    text-transform: uppercase;
  }
  .lockup__mark {
    width: 18px;
    height: 18px;
    background: var(--silver);
  }
  .lockup__role {
    display: flex;
    align-items: center;
    gap: 12px;
    font-size: 13px;
    font-weight: 400;
    letter-spacing: 5px;
    color: var(--grey-text);
    text-transform: uppercase;
  }
  .lockup__rule {
    width: 50px;
    height: 1px;
    background: var(--grey-text);
  }

  /* Back: photo + contacts */
  .portrait {
    position: absolute;
    left: 44px;
    top: 58px;
    width: 220px;
    height: 220px;
    border-radius: 50%;
    background: radial-gradient(circle at 50% 40%, var(--photo-light), var(--photo-dark));
  }
  .contact {
    position: absolute;
    left: 292px;
    top: 96px;
    color: var(--silver);
    font-size: 17px;
    font-weight: 300;
    line-height: 1.3;
  }
  .contact__list { list-style: none; }
  .contact__item {
    display: flex;
    align-items: center;
    gap: 8px;
  }
  .contact__icon {
    width: 14px;
    height: 14px;
    flex: none;
    fill: var(--silver);
  }
  .contact__address {
    margin-top: 14px;
    padding-left: 22px;
    font-style: normal;
  }
</style>
</head>
<body>
<main class="stage">
  <section class="card card--front" aria-label="Card front">
    <div class="lockup">
      <div class="lockup__name"><span class="lockup__mark"></span>Tobias Lendhart</div>
      <div class="lockup__role"><span class="lockup__rule"></span>Personal Trainer<span class="lockup__rule"></span></div>
    </div>
  </section>

  <section class="card card--back" aria-label="Card back">
    <div class="portrait" role="img" aria-label="Portrait photo of the trainer"></div>
    <div class="contact">
      <ul class="contact__list">
        <li class="contact__item">
          <svg class="contact__icon" viewBox="0 0 16 16" aria-hidden="true"><path d="M3 1h3l1.5 4-2 1.2a9 9 0 0 0 4.3 4.3L11 8.5l4 1.5v3a2 2 0 0 1-2 2A12 12 0 0 1 1 3a2 2 0 0 1 2-2z"/></svg>
          0162/3819204
        </li>
        <li class="contact__item">
          <svg class="contact__icon" viewBox="0 0 16 16" aria-hidden="true"><path d="M1 3h14v10H1z M2 4l6 5 6-5" fill="none" stroke="currentColor" style="stroke:#d6d6d8" stroke-width="1.4"/></svg>
          t.lendhart@postfeld.de
        </li>
        <li class="contact__item">
          <svg class="contact__icon" viewBox="0 0 16 16" aria-hidden="true"><circle cx="8" cy="8" r="7"/><path d="M1 8h14M8 1c-3 3-3 11 0 14M8 1c3 3 3 11 0 14" fill="none" stroke="#0e0e10" stroke-width="1"/></svg>
          www.tobiaslendhart.de
        </li>
      </ul>
      <address class="contact__address">
        Wiesengrundweg 14<br>
        80417 München
      </address>
    </div>
  </section>
</main>
</body>
</html>
```